Cat-products company needs smart, yet endearing, business card

We need a business card design for a new, but up-and-running, business based in Honolulu, Hawaii. The business is Purrnest Nook Co. Our first product is the most environmentally-friendly cat grass kit ever seen on the planet. Future products, currently in the R&D phase, will include a variety of exciting cat scratchers. We also do consulting work to help apartment-dwellers make their home more cat-friendly and, in the future, plan on doing full, custom installs of structure to create high walkways for cats.

Target Market(s)

Middle-aged, apartment-dwelling, middle-class workers who own 1 or more cats and who dote on them.

Industry/Entity Type

Pet Care

Contact Information for Business Card

A striking, professional, yet warm and friendly design is what we're after.

Font styles to use
Serif
Sans Serif
Other font styles liked:
• Comfortaa

Colors

Designer to choose colors to be used in the design.

Requirements
Must have
• The company logo: (see attachment)
• The company name: Purrnest Nook Co
• The web address: www.purrnestnookco.com
• Email: support@purrnestnookco.com
• Phone: +1 (808) 571 6023
• Update (Fri Jun 30 3017 7:45pm Hawaii Time) I would like, is possible, uploaded picture of the cat grass kit on the back of the card with some text along the lines of: Purrnest Nook Co - Maker Of The Leafiest Feline Sprout Set Yet
Nice to have
• A cat picture, cartoon, real or silhouette that illustrates cats in action and/or relaxing; ie using the apartment space to live, play and relax in and being well-contented.
• Most of the website is done in the font: Comfortaa. It might be nice to continue using this for brand consistency.
Should not have
• Hard-to-read fonts.

```html
<!DOCTYPE html>
<html lang="en">
<head>
<meta charset="utf-8">
<title>Purrnest Nook Co — Business Card</title>
<link rel="stylesheet" href="https://fonts.googleapis.com/css2?family=Comfortaa:wght@400;700&family=Nunito+Sans:wght@400;600&display=swap">
<style>
  :root {
    --brown: #56332c;
    --brown-deep: #4a2b25;
    --amber: #f7b016;
    --paper: #ffffff;
    --ink: #3b2420;
    --backdrop-light: #7c878b;
    --backdrop-dark: #4d575b;
  }
  * { box-sizing: border-box; margin: 0; padding: 0; }
  html, body { width: 1200px; height: 900px; overflow: hidden; }
  body {
    background: radial-gradient(ellipse at 60% 50%, var(--backdrop-light), var(--backdrop-dark));
    display: flex; align-items: center; justify-content: center; gap: 40px;
    font-family: "Nunito Sans", sans-serif;
  }
  .card {
    position: relative; width: 530px; height: 303px;
    border-radius: 16px; overflow: hidden;
    box-shadow: 0 10px 28px rgba(0,0,0,.35);
  }
  /* Front */
  .card--front { background: var(--brown); display: flex; flex-direction: column; align-items: center; justify-content: center; }
  .brand { display: flex; align-items: center; gap: 14px; white-space: nowrap; }
  .brand__mark { width: 30px; height: 30px; background: var(--paper); flex: none; }
  .brand__name { font-family: "Comfortaa", sans-serif; font-weight: 700; font-size: 38px; color: var(--amber); letter-spacing: .5px; }
  .front__web { margin-top: 22px; color: var(--paper); font-size: 15px; letter-spacing: .6px; }
  /* Back */
  .card--back { background: var(--paper); }
  .back__panel { position: absolute; inset: 0; }
  .back__brand { position: absolute; left: 36px; top: 40px; gap: 10px; }
  .back__brand .brand__mark { width: 20px; height: 20px; background: var(--brown); }
  .back__brand .brand__name { font-size: 21px; letter-spacing: 0; }
  .contacts { position: absolute; left: 36px; top: 128px; list-style: none; display: flex; flex-direction: column; gap: 10px; }
  .contact { display: flex; align-items: center; gap: 10px; font-size: 13px; color: var(--ink); white-space: nowrap; }
  .contact__icon { width: 20px; height: 20px; background: var(--brown); border-radius: 3px; display: flex; align-items: center; justify-content: center; flex: none; }
  .ribbon { position: absolute; right: 0; top: 84px; width: 240px; height: 48px; background: var(--amber);
    clip-path: polygon(22px 0, 100% 0, 100% 100%, 0 100%);
    display: flex; align-items: center; padding-left: 34px; }
  .ribbon__text { font-family: "Comfortaa", sans-serif; font-weight: 400; font-size: 19px; color: var(--ink); white-space: nowrap; }
</style>
</head>
<body>

  <section class="card card--front" aria-label="Card front">
    <div class="brand">
      <span class="brand__mark"></span>
      <span class="brand__name">Purrnest Nook Co</span>
    </div>
    <p class="front__web">www.purrnestnookco.com</p>
  </section>

  <section class="card card--back" aria-label="Card back">
    <svg class="back__panel" viewBox="0 0 530 303" preserveAspectRatio="none" aria-hidden="true">
      <polygon points="370,0 530,0 530,303 300,303" fill="var(--brown)"/>
    </svg>

    <div class="brand back__brand">
      <span class="brand__mark"></span>
      <span class="brand__name">Purrnest Nook Co</span>
    </div>

    <ul class="contacts">
      <li class="contact">
        <span class="contact__icon">
          <svg width="12" height="12" viewBox="0 0 24 24"><path fill="#fff" d="M6.6 10.8a15 15 0 0 0 6.6 6.6l2.2-2.2a1 1 0 0 1 1-.25 11.4 11.4 0 0 0 3.6.57 1 1 0 0 1 1 1V20a1 1 0 0 1-1 1A17 17 0 0 1 3 4a1 1 0 0 1 1-1h3.5a1 1 0 0 1 1 1c0 1.250.2 2.450.57 3.570a1 1 0 0 1-.25 1z"/></svg>
        </span>
        +1 (808) 571 6023
      </li>
      <li class="contact">
        <span class="contact__icon">
          <svg width="12" height="12" viewBox="0 0 24 24"><rect x="2" y="5" width="20" height="14" rx="1" fill="none" stroke="#fff" stroke-width="2"/><path d="M2 6l10 7 10-7" fill="none" stroke="#fff" stroke-width="2"/></svg>
        </span>
        support@purrnestnookco.com
      </li>
      <li class="contact">
        <span class="contact__icon">
          <svg width="12" height="12" viewBox="0 0 24 24"><circle cx="12" cy="12" r="9" fill="none" stroke="#fff" stroke-width="2"/><path d="M3 12h18M12 3c3 3 3 15 0 18M12 3c-3 3-3 15 0 18" fill="none" stroke="#fff" stroke-width="1.6"/></svg>
        </span>
        www.purrnestnookco.com
      </li>
    </ul>

    <div class="ribbon">
      <span class="ribbon__text">Purrnest Nook Co</span>
    </div>
  </section>

</body>
</html>
```